Two Wine Labels, One Red One White

We are looking to create a brand image for our wines. There are two requirements by law that we need, however beyond that, the creativity comes from the designer. Required are:
On The Red Label, Alcohol 14.1White Label Alcohol 12.5, The Size, 750ML
SO One label for the red wine with alcohol at 14.1 in a 750 ML Bottle, and one Label for white with alcohol at 12.5 in a 750 ML bottle.

Hi All:
I have some more clarity to assist in the design work.
The Brand Name of the wine is Valquine for both the red and the white
The name should appear as Valquine with the Brackets around phonetical as seen here
[val-keen] Both the word and the phonetical spelling should appear.
and can be seen on lexiquarry.com The Brand Name text can be black
Label should be very light grey, I am trying to capture a Stone grey or texture from stone, although, NOT Marble.
The Red Label, The word "Red" should be in red
The White Label, The word "White" should be in White, all the original remaining elements remain as originally posted.

I look forward to hearing from you for any additional questions.
Updates

Just added a logo Not really seeing what we are trying to achieve, maybe using the logo in the design may assist

Target Market(s)

Wine Aficionados

Requirements
Must have
• Details described in Project Description above, these are required by law. The Name of the Brand will be posted shortly. For the moment if you take the project, just place red on one label and white on the other.
Nice to have
• These two wines are from California (USA), so the Sierra Nevada Mountains could be an inspiration, to outline of California or coast line, a vineyard (of course), a vine...We are in silicon valley, so there is a map of silicon valley with the Bay and ocean, something from a map could work, or let your creativity flow and not use any of these concepts.
Should not have
• I do not not care for decorative fonts, however all else is open

```html
<!DOCTYPE html>
<html lang="en">
<head>
<meta charset="utf-8">
<title>Valquine Wine Labels – Red and White</title>
<link rel="stylesheet" href="https://fonts.googleapis.com/css2?family=Playfair+Display+SC:wght@700&family=Source+Sans+3:wght@400;600&display=swap">
<style>
  :root {
    --canvas-bg: #f4f4f4;
    --stone-grey: #e7e5e0;
    --stone-grey-soft: #efeeea;
    --stone-grey-clear: rgba(231,229,224,0);
    --ink: #111111;
    --red-wine: #e8262a;
    --red-deep: #b8202a;
    --sun-yellow: #f4d21f;
    --sun-yellow-clear: rgba(244,210,31,0);
    --white-green: #22b26b;
    --green-deep: #15824c;
    --tag-text: #ffffff;
  }
  * { box-sizing: border-box; margin: 0; padding: 0; }
  html, body {
    width: 1200px;
    height: 900px;
    overflow: hidden;
    background: var(--canvas-bg);
  }
  .label-set {
    position: relative;
    width: 1200px;
    height: 900px;
  }
  .wine-label {
    position: absolute;
    top: 138px;
    width: 420px;
    height: 624px;
    background: linear-gradient(160deg, var(--stone-grey-soft) 0%, var(--stone-grey) 100%);
    overflow: hidden;
    box-shadow: 0 2px 10px rgba(0,0,0,0.08);
  }
  .wine-label--red { left: 150px; --accent: var(--red-wine); --accent-deep: var(--red-deep); }
  .wine-label--white { left: 630px; --accent: var(--white-green); --accent-deep: var(--green-deep); }

  .label-art {
    position: absolute;
    inset: 0;
    background:
      radial-gradient(ellipse 48% 38% at 62% 52%, var(--stone-grey-soft) 55%, var(--stone-grey-clear) 100%),
      radial-gradient(ellipse 70% 45% at 75% 12%, var(--sun-yellow) 0%, var(--sun-yellow-clear) 70%),
      radial-gradient(ellipse 70% 45% at 80% 92%, var(--sun-yellow) 0%, var(--sun-yellow-clear) 70%),
      linear-gradient(90deg, var(--accent) 0%, var(--accent) 14%, var(--sun-yellow) 40%, var(--accent) 100%);
  }

  .wine-type {
    position: absolute;
    top: 156px;
    right: 0;
    width: 125px;
    height: 48px;
    background: var(--accent);
    color: var(--tag-text);
    font-family: "Source Sans 3", Arial, sans-serif;
    font-weight: 400;
    font-size: 30px;
    line-height: 48px;
    padding-left: 12px;
  }

  .brand {
    position: absolute;
    top: 272px;
    right: 7px;
    text-align: right;
  }
  .brand-name {
    font-family: "Playfair Display SC", "Times New Roman", serif;
    font-weight: 700;
    font-size: 58px;
    line-height: 1;
    color: var(--ink);
    letter-spacing: 0.5px;
  }
  .brand-phonetic {
    margin-top: 0;
    font-family: "Source Sans 3", Arial, sans-serif;
    font-weight: 400;
    font-size: 30px;
    line-height: 1.1;
    color: var(--accent-deep);
  }

  .legal {
    position: absolute;
    top: 425px;
    left: 295px;
    font-family: "Source Sans 3", Arial, sans-serif;
    font-weight: 400;
    font-size: 24px;
    line-height: 1.7;
    color: var(--ink);
  }
</style>
</head>
<body>
  <main class="label-set">
    <section class="wine-label wine-label--red">
      <div class="label-art" role="img" aria-label="Painted splash artwork of red and yellow vine leaves with red grape clusters framing a stone grey centre"></div>
      <p class="wine-type">Red</p>
      <div class="brand">
        <h1 class="brand-name">Valquine</h1>
        <p class="brand-phonetic">[val-keen]</p>
      </div>
      <div class="legal">
        <p class="legal-alcohol">Alcohol 14.1</p>
        <p class="legal-volume">750мл.</p>
      </div>
    </section>

    <section class="wine-label wine-label--white">
      <div class="label-art" role="img" aria-label="Painted splash artwork of green and yellow vine leaves with green grape clusters framing a stone grey centre"></div>
      <p class="wine-type">White</p>
      <div class="brand">
        <h2 class="brand-name">Valquine</h2>
        <p class="brand-phonetic">[val-keen]</p>
      </div>
      <div class="legal">
        <p class="legal-alcohol">Alcohol 12.5</p>
        <p class="legal-volume">750мл.</p>
      </div>
    </section>
  </main>
</body>
</html>
```